Halvex Power

We need a business card for "Halvex power". I have uploaded the logo, the color of the card should be according to the logo "Blackish".
Basically halvex power is a solar company.
Also we would like a sample file in which we can edit the information such names and contact details ourselves
The card would be two sided with following details
1- logo on front and underneath the logo there should be a line saying
"Cleaner . Cheaper . Power"
2-website i.e "www.halvexpowerco.com"
3- Icons for Facebook and Instagram that tells the clients we are available on both social sites.
4- name of the person with his/her designation underneath and email address
5-contact number
6- 1-800--- number with the extension number

its up to the designer how he/she places the details,but it must look professional

Industry/Entity Type

Business

Contact Information for Business Card

5-contact number

Requirements
Must have
• 1- logo on front and underneath the logo there should be a line saying
• "Cleaner . Cheaper . Power"
• 2-website i.e "www.halvexpowerco.com"
• 3- Icons for Facebook and Instagram that tells the clients we are available on both social sites.
• 4- name of the person with his/her designation underneath and email address
• 5-contact number of the person
• 6- 1-800--- number with the extension number
• 7-card should be in black shade like the logo

```html
<!DOCTYPE html>
<html lang="en">
<head>
<meta charset="utf-8">
<title>Halvex Power — Business Card</title>
<link href="https://fonts.googleapis.com/css2?family=Oswald:wght@500&family=Roboto:ital,wght@0,400;0,700;1,400&display=swap" rel="stylesheet">
<style>
  :root {
    --bg: #141414;
    --card-dark-1: #3a4656;
    --card-dark-2: #1b2330;
    --green: #7dc242;
    --white: #ffffff;
    --white-soft: #c9d0d8;
    --ink: #4a4a4a;
    --ink-soft: #777777;
  }
  * { margin: 0; padding: 0; box-sizing: border-box; }
  html, body {
    width: 1200px; height: 963px; overflow: hidden;
    background: var(--bg);
    font-family: "Roboto", Arial, sans-serif;
  }
  .card {
    position: absolute; left: 250px;
    width: 700px; height: 400px;
    border-radius: 18px; overflow: hidden;
  }
  /* Front */
  .card-front { top: 51px; }
  .front-backdrop {
    position: absolute; inset: 0;
    background: linear-gradient(135deg, var(--card-dark-1) 0%, #28323f 50%, var(--card-dark-2) 100%);
  }
  .brand {
    position: absolute; left: 0; right: 0; top: 120px;
    display: flex; align-items: center; justify-content: center; gap: 18px;
  }
  .brand-dot {
    width: 58px; height: 58px; border-radius: 50%;
    background: var(--green);
  }
  .brand-name {
    font-weight: 700; font-size: 50px; color: var(--green);
    letter-spacing: 0.5px; line-height: 1;
  }
  .tagline {
    position: absolute; left: 0; right: 0; top: 196px; text-align: center;
    font-size: 15px; letter-spacing: 4px; color: var(--white-soft);
  }
  .front-social {
    position: absolute; left: 0; right: 0; top: 262px;
    display: flex; align-items: center; justify-content: center; gap: 22px;
    color: var(--white); font-size: 16px;
  }
  .social-item { display: flex; align-items: center; gap: 8px; }
  .social-mark {
    width: 16px; height: 16px; border-radius: 50%;
    border: 2px solid var(--white);
  }
  /* Back */
  .card-back { top: 512px; background: var(--white); }
  .person {
    position: absolute; right: 378px; top: 122px; text-align: right; white-space: nowrap;
  }
  .person-name {
    font-family: "Oswald", "Arial Narrow", sans-serif;
    font-weight: 500; font-size: 38px; color: var(--green);
    letter-spacing: 1px; line-height: 1;
  }
  .person-title {
    margin-top: 6px; font-size: 16px; font-style: italic; color: var(--ink-soft);
  }
  .divider {
    position: absolute; left: 352px; top: 100px;
    width: 2px; height: 120px; background: var(--green);
  }
  .contacts {
    position: absolute; left: 380px; top: 104px;
    list-style: none; font-size: 16px; color: var(--ink);
  }
  .contacts li { display: flex; align-items: center; gap: 10px; height: 28px; white-space: nowrap; }
  .contacts svg { width: 13px; height: 13px; fill: var(--green); flex: none; }
  .contacts .accent { color: var(--green); }
  .address {
    position: absolute; left: 0; right: 0; bottom: 52px; text-align: center;
    font-size: 16px; color: var(--ink);
  }
</style>
</head>
<body>
  <section class="card card-front">
    <div class="front-backdrop" role="img" aria-label="Dimmed photo of a modern office interior in dark blue-grey tones"></div>
    <div class="brand">
      <span class="brand-dot"></span>
      <span class="brand-name">Halvex Power</span>
    </div>
    <p class="tagline">Cleaner . Cheaper . Power</p>
    <div class="front-social">
      <span class="social-item"><span class="social-mark"></span>/halvexpower</span>
      <span class="social-item"><span class="social-mark"></span>@halvexpower</span>
      <span class="front-tollfree">1-800-555-0199 ext. 204</span>
    </div>
  </section>

  <section class="card card-back">
    <div class="person">
      <h1 class="person-name">MARLO FENWICK</h1>
      <p class="person-title">President</p>
    </div>
    <div class="divider"></div>
    <ul class="contacts">
      <li><svg viewBox="0 0 24 24"><path d="M6.6 10.8a15.1 15.1 0 0 0 6.6 6.6l2.2-2.2a1 1 0 0 1 1-.25 11.4 11.4 0 0 0 3.6.57 1 1 0 0 1 1 1V20a1 1 0 0 1-1 1A17 17 0 0 1 3 4a1 1 0 0 1 1-1h3.5a1 1 0 0 1 1 1c0 1.25.2 2.45.57 3.6a1 1 0 0 1-.25 1z"/></svg><span>1-833-HXSOLAR</span></li>
      <li><svg viewBox="0 0 24 24"><path d="M7 1h10a2 2 0 0 1 2 2v18a2 2 0 0 1-2 2H7a2 2 0 0 1-2-2V3a2 2 0 0 1 2-2zm0 3v14h10V4z"/></svg><span>1-833-555-0142</span></li>
      <li><svg viewBox="0 0 24 24"><path d="M2 4h20v16H2zm2 2v.5l8 5 8-5V6zm0 2.9V18h16V8.9l-8 5z"/></svg><span>info@halvexpowerco.com</span></li>
      <li><svg viewBox="0 0 24 24"><path d="M12 2a10 10 0 1 0 0 20 10 10 0 0 0 0-20zm0 2c.9 0 2.2 1.8 2.8 5H9.2C9.8 5.8 11.1 4 12 4zM4.3 11h3a17 17 0 0 0 0 2h-3a8 8 0 0 1 0-2zm11.4 0h4a8 8 0 0 1 0 2h-4a17 17 0 0 0 0-2zM9 11h6a15 15 0 0 1 0 2H9a15 15 0 0 1 0-2zm.2 4h5.6c-.6 3.2-1.9 5-2.8 5s-2.2-1.8-2.8-5z"/></svg><span>www.<span class="accent">halvexpowerco</span>.com</span></li>
    </ul>
    <p class="address">14 Ridgeline Commerce Way Cedar Flats T2K 4M9</p>
  </section>
</body>
</html>
```